Local Roofing/Construction company business needs new biz card design

We need a new business card design, current cards are from the start of this operation and generic at best. We are a local Construction Company (General Contractor) with a majority of our work originating from insurance claims-exterior finish work is the main focus (Roofs-Siding-Gutters etc). Heavily involved with homeowners and the low ball offers they receive from insurance company's after a insurable event takes place. I have attached some of our original logo file(s) below.

```html
<!DOCTYPE html>
<html lang="en">
<head>
<meta charset="utf-8">
<title>Ironvale Construction – Business Card</title>
<link href="https://fonts.googleapis.com/css2?family=Montserrat:wght@400;500;700;800&display=swap" rel="stylesheet">
<style>
  :root {
    --bg: #2a2b2e;
    --card: #0d0d0e;
    --card-edge: #4cc46a;
    --green: #4cc46a;
    --white: #f2f2f2;
    --emboss: #1f1f21;
  }
  * { box-sizing: border-box; margin: 0; padding: 0; }
  html, body { width: 1200px; height: 900px; overflow: hidden; }
  body {
    background: var(--bg);
    font-family: "Montserrat", sans-serif;
    display: flex;
    flex-direction: column;
    align-items: center;
    justify-content: center;
    gap: 40px;
  }
  .card {
    position: relative;
    width: 700px;
    height: 400px;
    background: var(--card);
    border: 5px solid var(--card-edge);
    border-radius: 30px;
    overflow: hidden;
  }
  .brand {
    display: flex;
    align-items: center;
    gap: 16px;
    font-weight: 800;
    text-transform: uppercase;
    letter-spacing: 0.04em;
    white-space: nowrap;
  }
  .brand-mark { display: block; background: currentColor; flex: none; }

  /* front */
  .card-front {
    display: flex;
    align-items: center;
    justify-content: center;
  }
  .card-front .brand { color: var(--emboss); font-size: 36px; }
  .card-front .brand-mark { width: 34px; height: 34px; }

  /* back */
  .card-back .brand {
    position: absolute;
    top: 62px;
    right: 52px;
    color: var(--green);
    font-size: 24px;
    gap: 12px;
  }
  .card-back .brand-mark { width: 22px; height: 22px; }
  .person {
    position: absolute;
    left: 52px;
    top: 200px;
  }
  .person-name {
    color: var(--green);
    font-weight: 700;
    font-size: 30px;
    line-height: 1.1;
  }
  .person-title {
    color: var(--white);
    font-weight: 400;
    font-size: 16px;
    margin-top: 4px;
  }
  .rule {
    position: absolute;
    left: 52px;
    right: 52px;
    top: 282px;
    height: 2px;
    background: var(--green);
  }
  .contacts {
    position: absolute;
    left: 52px;
    right: 52px;
    top: 300px;
    display: flex;
    align-items: stretch;
    justify-content: space-between;
    color: var(--white);
    font-size: 13px;
    line-height: 1.75;
    white-space: nowrap;
  }
  .contact-group { display: flex; flex-direction: column; justify-content: center; }
  .contact-line { display: flex; align-items: center; gap: 9px; }
  .contact-line svg { width: 13px; height: 13px; fill: var(--green); flex: none; }
  .divider { width: 2px; background: var(--green); flex: none; }
</style>
</head>
<body>

  <section class="card card-front" aria-label="Card front">
    <div class="brand"><span class="brand-mark"></span>Ironvale Construction</div>
  </section>

  <section class="card card-back" aria-label="Card back">
    <div class="brand"><span class="brand-mark"></span>Ironvale Construction</div>

    <div class="person">
      <p class="person-name">Jordan Hale</p>
      <p class="person-title">Managing Director</p>
    </div>

    <div class="rule"></div>

    <div class="contacts">
      <div class="contact-group">
        <p class="contact-line">
          <svg viewBox="0 0 16 16" aria-hidden="true"><path d="M1 3h14v10H1z M1 3l7 6 7-6" fill="none" stroke="#4cc46a" stroke-width="1.6"/></svg>
          info@ironvalebuild.com
        </p>
        <p class="contact-line">
          <svg viewBox="0 0 16 16" aria-hidden="true"><circle cx="8" cy="8" r="6.5" fill="none" stroke="#4cc46a" stroke-width="1.6"/><path d="M1.5 8h13M8 1.5c-3 3.5-3 9.5 0 13M8 1.5c3 3.5 3 9.5 0 13" fill="none" stroke="#4cc46a" stroke-width="1.2"/></svg>
          www.ironvalebuild.com
        </p>
      </div>
      <span class="divider"></span>
      <div class="contact-group">
        <p class="contact-line">
          <svg viewBox="0 0 16 16" aria-hidden="true"><path d="M2 5c0-2 2-3 6-3s6 1 6 3v1h-3V5H5v1H2z M3 8h10l1 6H2z"/></svg>
          800-555-0142
        </p>
        <p class="contact-line">
          <svg viewBox="0 0 16 16" aria-hidden="true"><rect x="4" y="1" width="8" height="14" rx="1.5" fill="none" stroke="#4cc46a" stroke-width="1.6"/><circle cx="8" cy="12.5" r="0.9"/></svg>
          800-555-0142
        </p>
      </div>
      <span class="divider"></span>
      <div class="contact-group">
        <p>418 Meadow Park Rd, #12</p>
        <p>Fairview, OH 43000</p>
      </div>
    </div>
  </section>

</body>
</html>
```